Business Card Design

New business card design

Target Market(s)

Residential & Commercial Property Managers

Industry/Entity Type

Plumbing Services

Contact Information for Business Card

Name - Rowan Keddle, title - Director, Phone Number - 0431 286 517, email - rowan@tbk-plumbing.com.au, Company ABN - 73 215 904 386,

Font styles to use
Sans Serif

Colors
0054AA
0677BA
7BADD7
CADEEF
E8F1F8

```html
<!DOCTYPE html>
<html lang="en">
<head>
<meta charset="utf-8">
<title>TBK Plumbing Services – Business Card</title>
<link href="https://fonts.googleapis.com/css2?family=Montserrat:wght@400;500;700&display=swap" rel="stylesheet">
<style>
  :root {
    --backdrop: #161718;
    --card-white: #ffffff;
    --card-navy: #1c222b;
    --ink: #1c222b;
    --ink-body: #111418;
    --water: #2aa4e0;
    --brand-blue: #3d7cc6;
    --tagline-grey: #6b625c;
  }
  * { margin: 0; padding: 0; box-sizing: border-box; }
  html, body {
    width: 1200px;
    height: 1059px;
    overflow: hidden;
    background: var(--backdrop);
    font-family: "Montserrat", Arial, sans-serif;
  }
  .canvas { position: relative; width: 1200px; height: 1059px; }

  .card { position: absolute; border-radius: 22px; overflow: hidden; }
  .card--front { left: 256px; top: 89px; width: 688px; height: 391px; background: var(--card-white); }
  .card--back  { left: 253px; top: 546px; width: 695px; height: 395px; background: var(--card-navy); }

  .brand {
    position: absolute; left: 0; right: 0;
    display: flex; align-items: center; justify-content: center; gap: 14px;
  }
  .brand__dot { width: 22px; height: 22px; border-radius: 50%; background: var(--water); flex: none; }
  .brand__name { font-weight: 500; font-size: 38px; letter-spacing: 1px; white-space: nowrap; }
  .card--front .brand { top: 92px; }
  .card--front .brand__name { color: var(--ink); }
  .card--back .brand { top: 168px; }
  .card--back .brand__name { color: var(--brand-blue); }

  .holder {
    position: absolute; right: calc(688px - 324px); top: 242px; text-align: right;
  }
  .holder__name { font-weight: 700; font-size: 22px; color: var(--ink); line-height: 1.1; }
  .holder__title { font-size: 13px; color: var(--ink-body); margin-top: 4px; }

  .divider { position: absolute; left: 342px; top: 242px; width: 2px; height: 67px; background: var(--ink-body); }

  .contacts { position: absolute; left: 358px; top: 236px; list-style: none; }
  .contacts__item {
    display: flex; align-items: center; gap: 8px;
    height: 27px; font-size: 13.5px; color: var(--ink-body);
  }
  .contacts__icon { width: 16px; height: 16px; flex: none; }

  .abn {
    position: absolute; left: 0; right: 0; top: 346px; text-align: center;
    font-size: 16px; color: var(--ink-body);
  }
  .abn strong { font-weight: 700; }
</style>
</head>
<body>
<main class="canvas">

  <section class="card card--front" aria-label="Business card front">
    <div class="brand">
      <span class="brand__dot"></span>
      <span class="brand__name">TBK Plumbing Services</span>
    </div>

    <div class="holder">
      <p class="holder__name">Rowan Keddle</p>
      <p class="holder__title">Director</p>
    </div>

    <div class="divider"></div>

    <ul class="contacts">
      <li class="contacts__item">
        <svg class="contacts__icon" viewBox="0 0 16 16" aria-hidden="true">
          <path d="M3.5 1.5 L6 4 L4.6 6 C5.5 8 8 10.5 10 11.4 L12 10 L14.5 12.5 L12.8 14.3 C8 14 2 8 1.7 3.2 Z" fill="#111418"/>
          <path d="M9.5 2.5 A4 4 0 0 1 13.5 6.5 M9.5 0.8 A5.7 5.7 0 0 1 15.2 6.5" stroke="#111418" stroke-width="1.3" fill="none"/>
        </svg>
        <span>0431 286 517</span>
      </li>
      <li class="contacts__item">
        <svg class="contacts__icon" viewBox="0 0 16 16" aria-hidden="true">
          <rect x="2" y="4" width="12" height="8.5" rx="1" fill="#111418"/>
          <path d="M2.5 4.5 L8 8.5 L13.5 4.5" stroke="#fff" stroke-width="1.1" fill="none"/>
        </svg>
        <span>rowan@tbk-plumbing.com.au</span>
      </li>
      <li class="contacts__item">
        <svg class="contacts__icon" viewBox="0 0 16 16" aria-hidden="true">
          <circle cx="8" cy="8" r="6.5" fill="none" stroke="#111418" stroke-width="1.4"/>
          <path d="M4 4.5 C6 5 6 7 5 8 C4.5 9 6 10 6.5 12 L4 11 Z M9 3 C10.5 4 11 5.5 12.5 6 L12 9 C11 10 10 11 9.5 13 L9 9 L8 7 Z" fill="#111418"/>
        </svg>
        <span>www.tbk-plumbing.com.au</span>
      </li>
    </ul>

    <p class="abn"><strong>ABN</strong> - 73 215 904 386</p>
  </section>

  <section class="card card--back" aria-label="Business card back">
    <div class="brand">
      <span class="brand__dot"></span>
      <span class="brand__name">TBK Plumbing Services</span>
    </div>
  </section>

</main>
</body>
</html>
```